I have a logo and need to design the business card and stationery.
Updates

The uploaded logo image named as GREYMARSH CONSTRUCTION which is to be replaced to GREYMARSH CONTRACTS. Kindly add below details and submit the designs- Company name- Greymarsh Engineering Contracts LLP Name & Post- Kelvan Joshi (Designated Partner) Address- Block No.317, Wing C, Tulvo Trade Court, Manek Pural Road, Ruparel Industrial Estate, Goregaon(E), Mumbai - 400 063 Contact- +91 97415 60382 Email- kelvanjoshi@mailbrook.example Website- www.greymarshcontracts.example Contact for Letterhead- +91-22-28754193

Hi Tovin Rahul, We are liking your Design #28860835. We have suggested some changes which are mentioned in feedback. Kindly revert with it asap to finalize this design.

Colors

Designer to choose colors to be used in the design.

```html
<!DOCTYPE html>
<html lang="en">
<head>
<meta charset="utf-8">
<title>Greymarsh Contracts — Letterhead</title>
<link rel="stylesheet" href="https://fonts.googleapis.com/css2?family=Montserrat:wght@400;700&family=Open+Sans:wght@400&display=swap">
<style>
  :root {
    --backdrop: #d9d9d9;
    --paper: #f7f7f7;
    --ink: #1a1a1a;
    --text: #4a4a4a;
    --muted: #5c5c5c;
    --rule: #8ea3b5;
    --sign-fill: #e4e4e4;
  }
  * { margin: 0; padding: 0; box-sizing: border-box; }
  html, body { width: 1200px; height: 884px; overflow: hidden; background: var(--backdrop); }
  .letterhead {
    position: absolute; left: 303px; top: 22px;
    width: 594px; height: 840px;
    background: var(--paper);
    box-shadow: 0 6px 18px rgba(0,0,0,0.18);
    font-family: "Open Sans", sans-serif;
    color: var(--text);
  }
  .brand {
    position: absolute; top: 56px; right: 56px;
    display: flex; align-items: center; gap: 10px;
    font-family: "Montserrat", sans-serif; font-weight: 700;
    font-size: 17px; letter-spacing: 1px; color: var(--ink);
  }
  .brand-square { width: 30px; height: 30px; background: var(--ink); }
  .letter-body {
    position: absolute; top: 150px; left: 64px; right: 64px;
    font-size: 10.5px; line-height: 1.6;
  }
  .salutation { margin-bottom: 10px; }
  .letter-body p.para { margin-bottom: 12px; }
  .closing { margin-top: 16px; }
  .signature {
    width: 110px; height: 48px; margin-top: 12px;
    background: var(--sign-fill); border-radius: 3px;
  }
  .contact-bar {
    position: absolute; left: 64px; right: 64px; bottom: 52px;
    display: flex; align-items: center; gap: 20px;
    font-family: "Montserrat", sans-serif; font-size: 10.5px; color: var(--muted);
    line-height: 1.45;
  }
  .contact-group div { display: flex; align-items: center; gap: 6px; }
  .contact-group svg { width: 10px; height: 10px; fill: var(--ink); flex: none; }
  .divider { width: 1px; height: 30px; background: var(--rule); }
</style>
</head>
<body>
  <main class="letterhead">
    <header class="brand">
      <span class="brand-square"></span>
      <span class="brand-name">GREYMARSH CONTRACTS</span>
    </header>

    <section class="letter-body">
      <p class="salutation">Dear customer,</p>
      <p class="para">Lorem ipsum dolor sit amet, consectetur adipisicing elit, sed do eiusmod tempor incididunt ut labore et dolore magna aliqua. Ut enim ad minim veniam, quis nostrud exercitation ullamco laboris nisi ut aliquip ex ea commodo consequat. Duis aute irure dolor in reprehenderit in voluptate velit esse cillum dolore eu fugiat nulla pariatur. Excepteur sint occaecat cupidatat non proident, sunt in culpa qui officia deserunt mollit anim id est laborum.</p>
      <p class="para">Lorem ipsum dolor sit amet, consectetur adipisicing elit, sed do eiusmod tempor incididunt ut labore et dolore magna aliqua. Ut enim ad minim veniam, quis nostrud exercitation ullamco laboris nisi ut aliquip ex ea commodo consequat. Duis aute irure dolor in reprehenderit in voluptate velit esse cillum dolore eu fugiat nulla pariatur. Excepteur sint occaecat cupidatat non proident, sunt in culpa qui officia deserunt mollit anim id est laborum.</p>
      <p class="para">Lorem ipsum dolor sit amet, consectetur adipisicing elit, sed do eiusmod tempor incididunt ut labore et dolore magna aliqua. Ut enim ad minim veniam, quis nostrud exercitation ullamco laboris nisi ut aliquip ex ea commodo consequat. Duis aute irure dolor in reprehenderit in voluptate velit esse cillum dolore eu fugiat nulla pariatur. Excepteur sint occaecat cupidatat non proident, sunt in culpa qui officia deserunt mollit anim id est laborum.</p>
      <p class="para">Lorem ipsum dolor sit amet, consectetur adipisicing elit, sed do eiusmod tempor incididunt ut labore et dolore magna aliqua. Ut enim ad minim veniam, quis nostrud exercitation ullamco laboris nisi ut aliquip ex ea commodo consequat. Duis aute irure dolor in reprehenderit.</p>
      <p class="closing">Yours Sincerely,</p>
      <div class="signature" role="img" aria-label="Handwritten signature"></div>
    </section>

    <footer class="contact-bar">
      <div class="contact-group">
        <div><svg viewBox="0 0 10 10"><path d="M2 0.5 L3.6 0.5 L4.2 3 L3 3.8 Q4 6 6.2 7 L7 5.8 L9.5 6.4 L9.5 8 Q9.5 9.5 8 9.5 Q1 9 0.5 2 Q0.5 0.5 2 0.5Z"/></svg>+56927304481</div>
        <div><svg viewBox="0 0 10 10"><rect x="2.5" y="0.5" width="5" height="3"/><rect x="0.5" y="3.5" width="9" height="4"/><rect x="2.5" y="6.5" width="5" height="3" fill="#fff" stroke="#1a1a1a"/></svg>+56927304481</div>
      </div>
      <span class="divider"></span>
      <div class="contact-group">
        <div><svg viewBox="0 0 10 10"><rect x="0.5" y="2" width="9" height="6.5"/><path d="M0.8 2.3 L5 5.6 L9.2 2.3" stroke="#fff" stroke-width="0.9" fill="none"/></svg>info@northpier.example</div>
        <div><svg viewBox="0 0 10 10"><circle cx="5" cy="5" r="4.3" fill="none" stroke="#1a1a1a" stroke-width="1.2"/><path d="M0.7 5 H9.3 M5 0.7 Q2 5 5 9.3 M5 0.7 Q8 5 5 9.3" stroke="#1a1a1a" stroke-width="0.9" fill="none"/></svg>www.northpier.example</div>
      </div>
      <span class="divider"></span>
      <div class="contact-group">
        <div>14 Harlow Bend Drive, Land</div>
        <div>Cedarvale Hill, ON L7T 3K2</div>
      </div>
    </footer>
  </main>
</body>
</html>
```